Business card for medical clinic

I need an upmarket, modern medical/health business card for my clinic

Contact Information for Business Card

name, address, email, qr code

```html
<!DOCTYPE html>
<html lang="en">
<head>
<meta charset="utf-8">
<title>Corvane Health Clinic – Business Card</title>
<link rel="stylesheet" href="https://fonts.googleapis.com/css2?family=EB+Garamond:wght@400;500&display=swap">
<style>
  :root {
    --backdrop: #2b2c2f;
    --card: #1d2230;
    --card-edge: #252b3b;
    --silver: #9aa0aa;
    --accent: #1fa3e6;
    --accent-deep: #1a4f9c;
    --ink-light: #e8ecf2;
  }
  * { margin: 0; padding: 0; box-sizing: border-box; }
  html, body {
    width: 1200px; height: 852px; overflow: hidden;
    background: var(--backdrop);
    font-family: "EB Garamond", Georgia, serif;
  }
  .stage {
    width: 1200px; height: 852px;
    display: flex; align-items: center; justify-content: center; gap: 40px;
  }
  .card {
    position: relative;
    width: 540px; height: 310px;
    background: linear-gradient(160deg, var(--card-edge), var(--card));
    border-radius: 22px;
    overflow: hidden;
    box-shadow: 0 10px 30px rgba(0,0,0,.45);
  }
  /* Front */
  .card-front { display: flex; align-items: center; justify-content: center; }
  .front-wordmark {
    font-size: 40px; font-weight: 500; letter-spacing: 3px;
    color: var(--silver); text-transform: uppercase; text-align: center; line-height: 1.1;
  }
  /* Back */
  .brand-emblem-area {
    position: absolute; right: -30px; top: 10px;
    width: 300px; height: 290px; border-radius: 50%;
    background: radial-gradient(circle at 55% 55%, rgba(31,163,230,.18), rgba(26,79,156,.08) 55%, transparent 72%);
  }
  .back-wordmark {
    position: absolute; left: 34px; top: 38px;
    font-size: 19px; font-weight: 500; letter-spacing: 1.5px;
    color: var(--accent); text-transform: uppercase;
  }
  .holder { position: absolute; left: 34px; top: 118px; }
  .holder-name {
    font-size: 24px; font-weight: 400; letter-spacing: 1.5px;
    color: var(--accent); text-transform: uppercase; line-height: 1;
  }
  .holder-role { font-size: 15px; color: var(--ink-light); margin-top: 4px; }
  .contact-list { list-style: none; position: absolute; left: 34px; top: 186px; }
  .contact-item {
    display: flex; align-items: center; gap: 10px;
    font-size: 15px; color: var(--ink-light); height: 23px;
  }
  .contact-icon { width: 13px; height: 13px; fill: var(--accent); flex: none; }
  .contact-address { margin-top: 6px; font-size: 16px; }
</style>
</head>
<body>
<main class="stage">
  <section class="card card-front" aria-label="Card front">
    <h1 class="front-wordmark">Corvane Health<br>Clinic</h1>
  </section>

  <section class="card card-back" aria-label="Card back">
    <div class="brand-emblem-area" role="img" aria-label="Brand emblem decoration area"></div>
    <p class="back-wordmark">Corvane Health Clinic</p>
    <div class="holder">
      <h2 class="holder-name">Daniel Hartley</h2>
      <p class="holder-role">Managing Director</p>
    </div>
    <ul class="contact-list">
      <li class="contact-item">
        <svg class="contact-icon" viewBox="0 0 24 24" aria-hidden="true"><path d="M6.6 10.8a15 15 0 0 0 6.6 6.6l2.2-2.2c.3-.3.7-.4 1-.2 1.1.4 2.3.6 3.6.6.6 0 1 .4 1 1V20c0 .6-.4 1-1 1A17 17 0 0 1 3 4c0-.6.4-1 1-1h3.5c.6 0 1 .4 1 1 0 1.3.2 2.5.6 3.6.1.3 0 .7-.2 1z"/></svg>
        0123-456-78901
      </li>
      <li class="contact-item">
        <svg class="contact-icon" viewBox="0 0 24 24" aria-hidden="true"><path d="M2 5h20v14H2z M2 5l10 8 10-8" /></svg>
        hello@corvaneclinic.com
      </li>
      <li class="contact-item">
        <svg class="contact-icon" viewBox="0 0 24 24" aria-hidden="true"><circle cx="12" cy="12" r="10"/></svg>
        www.corvaneclinic.com
      </li>
      <li class="contact-item contact-address">48, Elm Row, Larkfield 20415</li>
    </ul>
  </section>
</main>
</body>
</html>
```